Make attractive Packaging label for NUT BUTTERS jars

We at Velora Pantry are launching our own line of NUT BUTTERS. We will be serving them in GLASS JARS ready packaged. I need attractive luxurious design for glass jar and should be designed ready to print.
I have attached glass jar pictures and measurement sheet.
My company logo has been attached. Also company details can be found on our facebook page.
product will be

ALMOND BUTTER
CASHEW BUTTER
PEANUT BUTTER
HAZELNUT BUTTER.

Industry/Entity Type

Retail

```html
<!DOCTYPE html>
<html lang="en">
<head>
<meta charset="utf-8">
<title>Velora Pantry – Peanut Butter Jar Label</title>
<link href="https://fonts.googleapis.com/css2?family=Open+Sans:wght@400;600;700;800&display=swap" rel="stylesheet">
<style>
  :root {
    --label-red: #c0071a;
    --label-cream: #fcf9ec;
    --stripe-pink: #f27ac0;
    --ink-dark: #1d1513;
    --brand-amber: #c97d22;
    --blob-brown: #2a1714;
    --badge-orange: #f08a1c;
    --badge-green: #6bbf2a;
    --text-white: #ffffff;
  }
  * { margin: 0; padding: 0; box-sizing: border-box; }
  html, body { width: 1200px; height: 1000px; overflow: hidden; background: #ffffff; }
  body { font-family: "Open Sans", Arial, sans-serif; position: relative; }

  .jar-label { position: absolute; left: 0; top: 332px; width: 1200px; height: 271px; }
  .label-ground { position: absolute; inset: 0; }

  .contact-list { position: absolute; left: 36px; top: 40px; list-style: none; color: var(--ink-dark); font-size: 13px; line-height: 15px; }
  .contact-item { display: flex; align-items: flex-start; margin-bottom: 7px; }
  .contact-icon { width: 16px; height: 16px; margin-right: 8px; flex: none; fill: var(--ink-dark); }
  .contact-text { width: 290px; }

  .brand-name { position: absolute; left: 440px; top: 14px; width: 260px; text-align: center;
    color: var(--brand-amber); font-weight: 800; font-size: 54px; line-height: 58px; letter-spacing: -1px; }

  .product-blob { position: absolute; left: 566px; top: 158px; width: 200px; height: 112px; }
  .product-name { position: absolute; left: 590px; top: 166px; width: 130px; text-align: center; color: var(--text-white); }
  .product-name .nut { display: block; font-weight: 700; font-size: 40px; line-height: 44px; letter-spacing: -1px; }
  .product-name .kind { display: block; font-weight: 400; font-size: 22px; line-height: 24px; letter-spacing: 1px; }
  .nut-illustration { position: absolute; left: 700px; top: 204px; width: 92px; height: 56px; border-radius: 28px;
    background: linear-gradient(135deg, #e8c48a, #b07a3c 55%, #7a1e2c); }

  .badge-row { position: absolute; right: 74px; top: 32px; display: flex; gap: 28px; }
  .diet-badge { width: 66px; height: 66px; border-radius: 50%; border: 3px solid var(--blob-brown); }
  .diet-badge.gluten-free { background: var(--badge-orange); }
  .diet-badge.vegan, .diet-badge.natural { background: var(--badge-green); }

  .shop-blurb { position: absolute; left: 840px; top: 161px; width: 322px; color: var(--text-white);
    font-size: 13px; line-height: 17px; text-align: justify; }
</style>
</head>
<body>
<section class="jar-label">
  <svg class="label-ground" width="1200" height="271" viewBox="0 0 1200 271" aria-hidden="true">
    <rect width="1200" height="271" fill="var(--label-red)"/>
    <polygon points="0,18 1200,18 1200,96 0,240" fill="var(--label-cream)"/>
    <polygon points="0,240 1200,96 1200,108 0,252" fill="var(--stripe-pink)"/>
  </svg>

  <ul class="contact-list">
    <li class="contact-item">
      <svg class="contact-icon" viewBox="0 0 16 16"><path d="M8 0a5.5 5.5 0 0 0-5.5 5.5C2.5 10 8 16 8 16s5.5-6 5.5-10.5A5.5 5.5 0 0 0 8 0zm0 8a2.5 2.5 0 1 1 0-5 2.5 2.5 0 0 1 0 5z"/></svg>
      <span class="contact-text">Linden Court Market, 14 Harbour Row, Dublin, Ireland</span>
    </li>
    <li class="contact-item">
      <svg class="contact-icon" viewBox="0 0 16 16"><circle cx="8" cy="8" r="7" fill="none" stroke="#1d1513" stroke-width="1.6"/><path d="M1 8h14M8 1c-3 3-3 11 0 14M8 1c3 3 3 11 0 14" fill="none" stroke="#1d1513" stroke-width="1.2"/></svg>
      <span class="contact-text">www.velorapantry.ie</span>
    </li>
    <li class="contact-item">
      <svg class="contact-icon" viewBox="0 0 16 16"><path d="M0 3h16v10H0z"/><path d="M0 3l8 6 8-6" fill="none" stroke="#fcf9ec" stroke-width="1.3"/></svg>
      <span class="contact-text">hello@velorapantry.ie</span>
    </li>
    <li class="contact-item">
      <svg class="contact-icon" viewBox="0 0 16 16"><path d="M3 0l3 1 1 4-2 1.5c1 2 2.5 3.5 4.5 4.5L11 9l4 1 1 3-2 3C7 15 1 9 0 2z"/></svg>
      <span class="contact-text">353 87 000 4821<br>087 000 3164<br>087 000 4821</span>
    </li>
  </ul>

  <div class="brand-name">Velora<br>Pantry</div>

  <svg class="product-blob" viewBox="0 0 200 112" aria-hidden="true">
    <path d="M30 8C70-4 120 4 150 14c30 10 48 20 44 44-4 30-40 52-84 54C60 114 14 100 4 70-4 44 4 16 30 8z" fill="var(--blob-brown)"/>
  </svg>
  <div class="product-name"><span class="nut">Peanut</span><span class="kind">BUTTER</span></div>
  <div class="nut-illustration" role="img" aria-label="Illustration of peanuts in shells, red-skinned peanuts and green leaves"></div>

  <div class="badge-row">
    <div class="diet-badge gluten-free" role="img" aria-label="Gluten free badge"></div>
    <div class="diet-badge vegan" role="img" aria-label="Vegan badge"></div>
    <div class="diet-badge natural" role="img" aria-label="100% natural badge"></div>
  </div>

  <p class="shop-blurb">A unique Dublin's only exquisite edible Nuts, Seed and Dried Fruit shop. From sweet and savoury snacking nuts to raw healthy nuts &amp; seeds and Dried fruits.</p>
</section>
</body>
</html>
```